New Business Card Design Project

Use the flyer uploaded and website www.brightoakbuilders.com for inspiration.
List Our Services on Backside of business cards
Marcus Delling
Harborline Builders Inc.
Licensed General Contractors
858-471-6093

Contact Information for Business Card

Use the flyer uploaded and website www.brightoakbuilders.com for inspiration. List Our Services on Backside of business cards Marcus Delling Harborline Builders Inc. Licensed General Contractors 858-471-6093

```html
<!DOCTYPE html>
<html lang="en">
<head>
<meta charset="utf-8">
<title>Harborline Builders Business Card</title>
<link href="https://fonts.googleapis.com/css2?family=Cinzel:wght@500;700&family=Montserrat:wght@400;500&display=swap" rel="stylesheet">
<style>
  :root {
    --backdrop: #2a2a2b;
    --card-dark: #141415;
    --card-light: #242526;
    --ink: #f2f2f2;
    --rule: #e6e6e6;
  }
  * { margin: 0; padding: 0; box-sizing: border-box; }
  html, body { width: 1200px; height: 900px; overflow: hidden; }
  body {
    background: var(--backdrop);
    font-family: "Montserrat", sans-serif;
    color: var(--ink);
    position: relative;
  }
  .card {
    position: absolute;
    left: 250px;
    width: 700px;
    height: 400px;
    border-radius: 18px;
    background: linear-gradient(135deg, var(--card-dark) 0%, var(--card-light) 100%);
    overflow: hidden;
  }
  .card--front { top: 35px; }
  .card--back { top: 465px; }

  .brand-name {
    font-family: "Cinzel", serif;
    font-weight: 500;
    color: var(--ink);
    text-align: center;
    letter-spacing: 0.04em;
    white-space: nowrap;
  }
  .card--front .brand-name {
    position: absolute;
    left: 0; right: 0;
    top: 175px;
    font-size: 44px;
  }
  .card--back .brand-name {
    position: absolute;
    left: 0; right: 0;
    top: 70px;
    font-size: 34px;
  }

  .holder {
    position: absolute;
    top: 185px;
    right: 370px;
    text-align: right;
  }
  .holder__name {
    font-family: "Cinzel", serif;
    font-weight: 700;
    font-size: 30px;
    letter-spacing: 0.03em;
  }
  .holder__title {
    font-size: 19px;
    font-weight: 400;
    margin-top: 2px;
  }
  .divider {
    position: absolute;
    left: 350px;
    top: 185px;
    width: 1.5px;
    height: 90px;
    background: var(--rule);
  }
  .contact {
    position: absolute;
    left: 372px;
    top: 188px;
    list-style: none;
    font-size: 18px;
    font-weight: 500;
  }
  .contact li {
    display: flex;
    align-items: center;
    gap: 10px;
    height: 28px;
  }
  .contact svg { width: 16px; height: 16px; flex: none; }
  .contact .no-icon { padding-left: 26px; }

  .footer-rule {
    position: absolute;
    top: 335px;
    height: 1.5px;
    background: var(--rule);
  }
  .footer-rule--left { left: 0; width: 215px; }
  .footer-rule--right { right: 0; width: 215px; }
  .legal-name {
    position: absolute;
    top: 323px;
    left: 0; right: 0;
    text-align: center;
    font-size: 18px;
    font-weight: 400;
  }
</style>
</head>
<body>
  <section class="card card--front">
    <div class="brand-name">Harborline Builders</div>
  </section>

  <section class="card card--back">
    <div class="brand-name">Harborline Builders</div>

    <div class="holder">
      <div class="holder__name">Marcus Delling</div>
      <div class="holder__title">Licensed General Contractors</div>
    </div>

    <div class="divider"></div>

    <ul class="contact">
      <li>
        <svg viewBox="0 0 24 24" fill="none" stroke="currentColor" stroke-width="2" stroke-linejoin="round"><path d="M5 3h4l2 5-3 2a11 11 0 0 0 6 6l2-3 5 2v4a2 2 0 0 1-2 2A17 17 0 0 1 3 5a2 2 0 0 1 2-2z"/></svg>
        858-471-6093
      </li>
      <li>
        <svg viewBox="0 0 24 24" fill="none" stroke="currentColor" stroke-width="2"><rect x="2" y="5" width="20" height="14"/><path d="M2 5l10 8 10-8"/></svg>
        info@brightoakbuilders.com
      </li>
      <li>
        <svg viewBox="0 0 24 24" fill="none" stroke="currentColor" stroke-width="2"><circle cx="12" cy="12" r="10"/><path d="M2 12h20M12 2c3 3 3 17 0 20M12 2c-3 3-3 17 0 20"/></svg>
        www.brightoakbuilders.com
      </li>
      <li class="no-icon">www.brightoakbuilders.com</li>
    </ul>

    <div class="footer-rule footer-rule--left"></div>
    <div class="legal-name">Harborline Builders Inc.</div>
    <div class="footer-rule footer-rule--right"></div>
  </section>
</body>
</html>
```